Business Card Design

Brambleford Hearth is the name of my health coaching business. My tag line is "Where good health meets real life." I will be working with clients one-on-one and in groups. My target clients are women "of a certain age" who want to be more comfortable in their own skin. We will work together in a 6-month program. The coaching sessions will take place in my kitchen. I will also be conducting monthly cooking classes and field trips - to farmer's markets, speciality markets etc.. for my clients.
Updates

the business name is Brambleford Hearth - I'm not sure how the p got in there at the end of the name

Thank you

Please include the website - www.bramblefordhearth-example.com and the tag line:

Where good health meets real life on the business card.

Thank you

Please add the phone number to the business card - sorry, I forgot to state that in the original brief

(555) 217-4860

Target Market(s)

Women "of a certain age" who want to be more comfortable in their own skin

Industry/Entity Type

Cooking

Contact Information for Business Card

Brambleford Hearth
Where good health meets real life

Tessa Marlowe
Health Coach
(555) 217-4860

Font styles to use
Serif
Sans Serif

Requirements
Must have
• front & back design
I typical like soft colors - and have tended toward greens over time - I'm open although I would not like bright reds, yellows etc..

```html
<!DOCTYPE html>
<html lang="en">
<head>
<meta charset="utf-8">
<title>Brambleford Hearth — Business Card</title>
<link rel="stylesheet" href="https://fonts.googleapis.com/css2?family=Open+Sans:wght@400;600;700&family=Ubuntu:wght@400&family=Lora:wght@400&display=swap">
<style>
  :root {
    --brand-green: #12ad5f;
    --ink: #2b2b2b;
    --card-light: #ffffff;
    --card-shade: #e2e2e2;
    --canvas-bg: #eeeeea;
  }
  * { margin: 0; padding: 0; box-sizing: border-box; }
  html, body { width: 1200px; height: 894px; overflow: hidden; }
  body {
    background: var(--canvas-bg);
    font-family: "Open Sans", Arial, sans-serif;
    position: relative;
  }
  .card {
    position: absolute;
    top: 132px;
    width: 360px;
    height: 630px;
    border-radius: 22px;
    overflow: hidden;
    box-shadow: 0 6px 18px rgba(0,0,0,0.18);
  }
  .card-back { left: 180px; background: var(--brand-green); }
  .card-front {
    left: 660px;
    background: linear-gradient(180deg, var(--card-light) 0%, var(--card-light) 35%, var(--card-shade) 100%);
  }
  .brand-name {
    position: absolute;
    left: 34px;
    top: 40px;
    font-family: "Ubuntu", "Open Sans", sans-serif;
    font-variant: small-caps;
    font-size: 20px;
    letter-spacing: 3px;
    color: var(--brand-green);
    white-space: nowrap;
  }
  .tagline {
    position: absolute;
    left: 34px;
    top: 74px;
    font-family: "Lora", Georgia, serif;
    font-size: 13px;
    color: var(--ink);
    white-space: nowrap;
  }
  .name-tab {
    position: absolute;
    left: 0;
    top: 130px;
    width: 280px;
    height: 80px;
    background: var(--brand-green);
    border-radius: 0 40px 40px 0;
    color: #fff;
    padding: 15px 0 0 34px;
  }
  .person-name { font-weight: 700; font-size: 23px; letter-spacing: 1px; line-height: 1.2; white-space: nowrap; }
  .person-role { font-size: 13px; letter-spacing: 1.5px; }
  .contact-list {
    position: absolute;
    left: 30px;
    top: 330px;
    list-style: none;
  }
  .contact-item {
    display: flex;
    align-items: center;
    height: 40px;
    font-size: 12px;
    letter-spacing: 0.3px;
    color: var(--ink);
    text-transform: uppercase;
    white-space: nowrap;
  }
  .contact-icon { width: 20px; height: 20px; margin-right: 12px; flex: none; }
  .bottom-stripe {
    position: absolute;
    left: 0; right: 0; bottom: 0;
    height: 16px;
    background: var(--brand-green);
  }
</style>
</head>
<body>

<div class="card card-back" aria-label="Card back"></div>

<div class="card card-front" aria-label="Card front">
  <div class="brand-name">Brambleford Hearth</div>
  <div class="tagline">Where good health meets real life</div>

  <div class="name-tab">
    <div class="person-name">TESSA MARLOWE</div>
    <div class="person-role">HEALTH COACH</div>
  </div>

  <ul class="contact-list">
    <li class="contact-item">
      <svg class="contact-icon" viewBox="0 0 20 20"><circle cx="10" cy="10" r="9" fill="none" stroke="#12ad5f" stroke-width="1.6"/><rect x="6.5" y="7" width="7" height="6" rx="1" fill="none" stroke="#12ad5f" stroke-width="1.4"/><rect x="5.5" y="5.5" width="9" height="2" rx="1" fill="#12ad5f"/></svg>
      (555) 217-4860
    </li>
    <li class="contact-item">
      <svg class="contact-icon" viewBox="0 0 20 20"><circle cx="10" cy="10" r="9" fill="none" stroke="#12ad5f" stroke-width="1.6"/><path d="M7 5.5c-1 .8-1.3 2-.6 3.6 1 2.3 2.7 4 4.9 5 1.3.6 2.5.3 3.2-.7l-1.8-1.6-1.3.7c-1.2-.6-2.2-1.6-2.8-2.8l.7-1.3z" fill="#12ad5f"/></svg>
      (555) 217-4861
    </li>
    <li class="contact-item">
      <svg class="contact-icon" viewBox="0 0 20 20"><circle cx="10" cy="10" r="9" fill="#12ad5f"/><rect x="7" y="4.5" width="6" height="11" rx="1.2" fill="none" stroke="#fff" stroke-width="1.4"/></svg>
      hello@bramblefordhearth-example.com
    </li>
    <li class="contact-item">
      <svg class="contact-icon" viewBox="0 0 20 20"><circle cx="10" cy="10" r="9" fill="#12ad5f"/><circle cx="10" cy="10" r="5" fill="none" stroke="#fff" stroke-width="1.2"/><ellipse cx="10" cy="10" rx="2" ry="5" fill="none" stroke="#fff" stroke-width="1.1"/><line x1="5" y1="10" x2="15" y2="10" stroke="#fff" stroke-width="1.1"/></svg>
      www.bramblefordhearth-example.com
    </li>
    <li class="contact-item">
      <svg class="contact-icon" viewBox="0 0 20 20"><circle cx="10" cy="10" r="9" fill="none" stroke="#12ad5f" stroke-width="1.6"/><path d="M10 4.5a3.5 3.5 0 0 0-3.5 3.5c0 2.6 3.5 7 3.5 7s3.5-4.4 3.5-7A3.5 3.5 0 0 0 10 4.5z" fill="#12ad5f"/><circle cx="10" cy="8" r="1.2" fill="#fff"/></svg>
      48 Orchard Lane, Brambleford, USA
    </li>
  </ul>

  <div class="bottom-stripe"></div>
</div>

</body>
</html>
```